COVID-19 Accredited CME Impact Infographic

We want an infographic showing how much COVID-19 Continuing Medical Education we have accredited and its impact. Our website is at https://med.kelbrook.edu/cme/COVID19/education.html The attached document is intended to simply show the elements. You have complete freedom on design. We will be updating the numbers weekly so it is important that we have the files so that we can update it. This can be done in powerpoint, publisher, word, in-design, illustrator. Don't use crazy fonts that we wont have.

Target Market(s)

Internal to Kelbrook. We just want to show the impact of our work

Industry/Entity Type

Education

Requirements
Must have
• We must be able to update the numbers ourselves.

See attached document for the pieces that we want.

The sizes of the numbers in the attached are based on importance to us.
Nice to have
• Not mandatory but try to use these colors. https://med.kelbrook.edu/identity/color-palette.html

I was thinking that perhaps the big number could be done in traditional train. Like this: https://www.pixelvarda.com/image-illustration/flip-board-under-constuction-page-isolated-4816203957

```html
<!DOCTYPE html>
<html lang="en">
<head>
<meta charset="utf-8">
<title>COVID-19 CME Impact</title>
<link rel="stylesheet" href="https://fonts.googleapis.com/css2?family=Carlito:wght@400;700&family=Open+Sans:wght@400;600;700&display=swap">
<style>
  :root {
    --navy: #133f5a;
    --olive: #7a9a34;
    --cardinal: #8c1515;
    --cardinal-band: #8a1a1c;
    --periwinkle: #8fa9dc;
    --mint-light: #a9dcbc;
    --teal-dark: #3e8e8c;
    --white: #ffffff;
  }
  * { box-sizing: border-box; margin: 0; padding: 0; }
  html, body { width: 1200px; height: 923px; overflow: hidden; background: var(--white); }
  .infographic { position: relative; width: 1200px; height: 923px; background: var(--white); font-family: "Open Sans", sans-serif; }

  .header {
    position: absolute; left: 4px; top: 0; width: 1196px; height: 164px;
    background: linear-gradient(90deg, var(--teal-dark) 0%, #6cb8a4 30%, var(--mint-light) 55%, #7cc2a8 80%, #3c7f7a 100%);
  }
  .header-virus {
    position: absolute; right: 0; top: 0; width: 210px; height: 164px;
    background: radial-gradient(circle at 60% 45%, #b32a2a 0%, #7e1d24 40%, rgba(62,110,110,0) 72%);
  }
  .brand { position: absolute; left: 52px; top: 86px; display: flex; align-items: center; gap: 8px; }
  .brand-mark { width: 22px; height: 22px; background: var(--cardinal); }
  .brand-name { font-family: "Carlito", sans-serif; font-size: 24px; color: var(--cardinal); }
  .title {
    position: absolute; left: 317px; top: 38px;
    font-family: "Open Sans", sans-serif; font-weight: 400; font-size: 78px; line-height: 1;
    color: var(--white); letter-spacing: 1px;
  }

  .olive-figure { position: absolute; font-family: "Carlito", sans-serif; color: var(--olive); line-height: 1; }
  .states-count { left: 92px; top: 248px; font-size: 96px; }
  .states-label { left: 106px; top: 345px; font-size: 24px; }
  .countries-count { left: 690px; top: 258px; font-size: 96px; }
  .countries-label { left: 682px; top: 354px; font-size: 24px; }

  .map { position: absolute; }
  .map-us { left: 236px; top: 222px; width: 304px; height: 198px; border-radius: 22px 10px 40px 30px;
    background: linear-gradient(135deg, var(--navy) 0%, var(--periwinkle) 35%, var(--periwinkle) 65%, var(--navy) 100%); }
  .map-world { left: 812px; top: 226px; width: 318px; height: 182px; border-radius: 30px;
    background: radial-gradient(ellipse at 50% 45%, var(--navy) 0%, #2b5672 60%, rgba(19,63,90,0.15) 100%); }

  .legend { position: absolute; left: 132px; top: 438px; display: flex; gap: 22px; font-family: "Carlito", sans-serif; font-size: 23px; color: #111; }
  .legend-item { display: flex; align-items: center; gap: 9px; }
  .legend-swatch { width: 17px; height: 17px; border: 1.5px solid #555; }
  .swatch-cardinal { background: var(--cardinal); }
  .swatch-navy { background: var(--navy); }
  .swatch-periwinkle { background: var(--periwinkle); }
  .swatch-olive { background: var(--olive); }

  .learner-icon { position: absolute; width: 62px; background: var(--navy); opacity: 0.85; border-radius: 6px; }
  .icon-cme { left: 90px; top: 544px; height: 76px; }
  .icon-live { left: 89px; top: 648px; height: 82px; background: linear-gradient(180deg, var(--navy) 60%, #e8eef2 60%); }

  .learner-row { position: absolute; display: flex; align-items: baseline; gap: 22px; color: var(--navy); }
  .row-cme { left: 210px; top: 552px; }
  .row-live { left: 177px; top: 670px; }
  .learner-value { font-size: 56px; font-weight: 400; line-height: 1; }
  .learner-label { font-size: 30px; font-weight: 600; }

  .activities-label { position: absolute; left: 694px; top: 623px; font-family: "Carlito", sans-serif; font-size: 25px; line-height: 1.3; color: var(--olive); }
  .activities-count { position: absolute; left: 830px; top: 452px; font-family: "Open Sans", sans-serif; font-size: 268px; line-height: 1; color: var(--navy); letter-spacing: -6px; }

  .views-band { position: absolute; left: 4px; top: 785px; width: 1196px; height: 138px; background: var(--cardinal-band); }
  .views-icon { position: absolute; left: 64px; top: 14px; }
  .views-label { position: absolute; left: 289px; top: 14px; font-size: 25px; font-weight: 700; line-height: 36px; color: var(--white); }
  .views-count { position: absolute; left: 508px; top: -2px; font-size: 126px; font-weight: 700; line-height: 1.1; color: #f3f4f6; letter-spacing: -1px; }
</style>
</head>
<body>
<main class="infographic">
  <header class="header">
    <div class="header-virus" role="img" aria-label="Close-up illustration of a red coronavirus particle"></div>
    <div class="brand">
      <span class="brand-mark"></span>
      <span class="brand-name">Kelbrook Medicine</span>
    </div>
    <h1 class="title">COVID-19CME</h1>
  </header>

  <section class="reach">
    <div class="olive-figure states-count">26</div>
    <div class="olive-figure states-label">STATES</div>
    <div class="map map-us" role="img" aria-label="Map of the United States with states shaded by learner data"></div>
    <ul class="legend" aria-label="Map legend">
      <li class="legend-item"><span class="legend-swatch swatch-cardinal"></span>DATA</li>
      <li class="legend-item"><span class="legend-swatch swatch-navy"></span>DATA</li>
      <li class="legend-item"><span class="legend-swatch swatch-periwinkle"></span>DATA</li>
      <li class="legend-item"><span class="legend-swatch swatch-olive"></span>DATA</li>
    </ul>

    <div class="olive-figure countries-count">12</div>
    <div class="olive-figure countries-label">COUNTRIES</div>
    <div class="map map-world" role="img" aria-label="World map in navy"></div>
  </section>

  <section class="learners">
    <div class="learner-icon icon-cme" role="img" aria-label="Icon of a learner seated at a desk"></div>
    <div class="learner-row row-cme"><span class="learner-value">5,879</span><span class="learner-label">CME Learners</span></div>
    <div class="learner-icon icon-live" role="img" aria-label="Icon of a learner with a headset at a laptop"></div>
    <div class="learner-row row-live"><span class="learner-value">23,098</span><span class="learner-label">Live Learners</span></div>
  </section>

  <section class="activities">
    <div class="activities-label"># OF<br>ACTIVITIES</div>
    <div class="activities-count">23</div>
  </section>

  <section class="views-band">
    <svg class="views-icon" width="154" height="102" viewBox="0 0 154 102" aria-hidden="true">
      <path d="M30 100 H124 A28 28 0 0 0 128 44 A38 38 0 0 0 56 30 A32 32 0 0 0 22 58 A22 22 0 0 0 30 100 Z" fill="#ffffff"/>
      <path d="M68 44 L98 63 L68 82 Z" fill="#8a1a1c"/>
    </svg>
    <div class="views-label"># of total<br>on-demand<br>views</div>
    <div class="views-count">1,209,987</div>
  </section>
</main>
</body>
</html>
```